Toms welding and seed cleaning Business cards

Toms welding and seed cleaningWe clean wheat seed on farm with portable cleaners so the farmers have pure wheat seed to plant back for the next crop. We are certified to clean foundation, registered, and certified seed wheat. Our cleaners being portable make it easier for the farmers because we do it right on there farm so they don't have to haul it all to townWhen there is no wheat to clean we weld in the winter. We improve, add onto, and build new corrals. We also build sheds, cattle shelters, and wind breaks. Other welding is welcomed

Reason: I need to extend the deadline because I've been busy and not had my game together. I need more time figure out what I want yet

Industry/Entity Type

Agriculture

Contact Information for Business Card

Just "toms welding and seed cleaning" on front and other info on the back
On the back side I would like to have my address.
Morris Tulane
48213 W COUNTY RD 318
ISABELLA OK 73747
Phone #5804419362

Font styles to use
Sans Serif

Requirements
Must have
• list we are certified to clean foundation, registered, and certified wheat
• State that they are portable cleaners
• For the welding part list, add on to, improve on, and repair existing corrals and new corrals and other welding welcomed
Nice to have
• A wheat field with some metal corrals on the side with a nice classic looking barn for a background. Maybe some cattle in the corrals
• A nice looking farm yard would be good too

```html
<!DOCTYPE html>
<html lang="en">
<head>
<meta charset="utf-8">
<title>Toms Welding and Seed Cleaning – Business Cards</title>
<link rel="stylesheet" href="https://fonts.googleapis.com/css2?family=Montserrat:wght@500;700&display=swap">
<style>
  :root {
    --page: #ffffff;
    --ink: #050505;
    --white: #ffffff;
    --yellow: #f2ec12;
    --sky-deep: #2c4f8e;
    --sky-mid: #6f93c4;
    --sky-light: #c9d8ea;
    --field: #3f4a2a;
    --back-deep: #1d49a6;
    --back-mid: #0a86cf;
    --back-light: #3fb6e8;
  }
  * { box-sizing: border-box; margin: 0; padding: 0; }
  html, body { width: 1200px; height: 1000px; overflow: hidden; background: var(--page); }
  .canvas { position: relative; width: 1200px; height: 1000px; font-family: "Montserrat", sans-serif; }

  .card { position: absolute; overflow: hidden; }
  .card-front { left: 167px; top: 66px; width: 891px; height: 426px; }
  .card-back { left: 168px; top: 515px; width: 897px; height: 420px;
    background: linear-gradient(115deg, var(--back-deep) 0%, var(--back-mid) 55%, var(--back-light) 100%); }

  .field-photo { position: absolute; inset: 0;
    background: linear-gradient(180deg, var(--sky-light) 0%, var(--sky-mid) 30%, var(--sky-deep) 55%, var(--field) 100%); }
  .wave { position: absolute; inset: 0; width: 100%; height: 100%; }
  .wave path { fill: var(--ink); }

  .brand { position: absolute; right: 22px; top: 288px; width: 520px; height: 120px;
    font-family: "Montserrat", sans-serif; font-weight: 500; color: var(--white); }
  .brand-name { position: absolute; right: 112px; top: 0; font-size: 70px; line-height: 1; letter-spacing: -1px; }
  .brand-mark { position: absolute; right: 24px; top: 10px; width: 56px; height: 56px; border-radius: 50%; background: var(--yellow); }
  .brand-tagline { position: absolute; right: 0; top: 92px; font-size: 29px; line-height: 1; white-space: nowrap; }

  .back-title { position: absolute; left: 22px; top: 6px; white-space: nowrap;
    font-weight: 700; font-size: 35px; color: var(--yellow); letter-spacing: 3.3px; }
  .services { position: absolute; left: 22px; top: 58px; list-style: none; z-index: 2;
    font-weight: 500; font-size: 17.5px; line-height: 21px; color: var(--white);
    letter-spacing: 2.7px; word-spacing: 2px; white-space: nowrap; }
  .services li { margin-bottom: 17px; padding-left: 22px; text-indent: -22px; }
  .services li::before { content: "* "; }

  .phone { position: absolute; left: 18px; top: 393px; z-index: 2;
    font-weight: 500; font-size: 18px; color: var(--yellow); letter-spacing: 7.5px; }
  .contact { position: absolute; left: 594px; top: 308px; z-index: 2; font-style: normal;
    font-weight: 500; font-size: 19px; line-height: 27.5px; color: var(--yellow); letter-spacing: 1.9px; white-space: nowrap; }
  .contact .email { font-size: 17px; letter-spacing: 2.8px; }
</style>
</head>
<body>
<main class="canvas">
  <section class="card card-front" aria-label="Front of business card">
    <div class="field-photo" role="img" aria-label="Photograph of wheat ears against a blue cloudy sky"></div>
    <svg class="wave" viewBox="0 0 891 426" preserveAspectRatio="none" aria-hidden="true">
      <path d="M0,356 C90,380 150,405 240,400 C420,390 560,300 700,268 C790,250 850,262 891,288 L891,426 L0,426 Z"/>
    </svg>
    <div class="brand">
      <div class="brand-name">Toms</div>
      <div class="brand-mark" aria-hidden="true"></div>
      <div class="brand-tagline">Welding And Seed Cleaning</div>
    </div>
  </section>

  <section class="card card-back" aria-label="Back of business card">
    <h1 class="back-title">At Toms welding and seed cleaning...</h1>
    <ul class="services">
      <li>We use portable cleaners to clean your wheat seed&nbsp; so that you are<br>ready to plant the pure wheat seed for the next crop.</li>
      <li>You can get the cleaning done on your farms instead of hauling<br>it over to town.</li>
      <li>We are registered and certified professionals.</li>
      <li>&nbsp;We improve and build new corrals in winters.</li>
      <li>&nbsp;We can help you build sheds, cattle shelters, wind breaks, etc.</li>
      <li>&nbsp;Other welding jobs are also welcomed.</li>
    </ul>
    <svg class="wave" viewBox="0 0 897 420" preserveAspectRatio="none" aria-hidden="true">
      <path d="M0,352 C10,382 60,395 160,392 C330,386 480,300 620,262 C730,235 830,250 897,285 L897,420 L0,420 Z"/>
    </svg>
    <p class="phone">Call Us at 000-00-000</p>
    <address class="contact">
      Address: xyz xyz xyz 0000<br>
      zyx xyzxxxx yyyyyy zzzzzz<br>
      xxxxxxx yyyyy zzzzzz<br>
      <span class="email">Email: xyz@xyz.com</span>
    </address>
  </section>
</main>
</body>
</html>
```